Heritage Hollow Business Cards

Require a business card design. <br/><br/>Needs to include logo (either round or long version) plus these details:<br/>Maya Torvell<br/>Heritage Hollow<br/>maya@kelvadtrading.com.au<br/>02 6481 7395<br/>PO Box Glenwarra NSW 2791<br/>www.heritagehollow.com.au<br/><br/>I need in an editable format so that I can create for multiple staff members. <br/><br/>

Target Market(s)

We are an online store selling renovation products to home owners are builders. Looking for a classic classy design.

Industry/Entity Type

Home And Garden

Contact Information for Business Card

Maya Torvell
Heritage Hollow
maya@kelvadtrading.com.au
02 6481 7395
PO Box Glenwarra NSW 2791
www.heritagehollow.com.au

Colors

Designer to choose colors to be used in the design.

Requirements
Must have
• Must include Logo.

```html
<!DOCTYPE html>
<html lang="en">
<head>
<meta charset="utf-8">
<title>Heritage Hollow Business Cards</title>
<link href="https://fonts.googleapis.com/css2?family=Arimo:wght@400;700&display=swap" rel="stylesheet">
<style>
  :root {
    --page-bg: #2b2b2b;
    --card-bg: #1f2022;
    --card-back-bg: #19191b;
    --ink: #f2f2f2;
    --ink-soft: #d9d9d9;
    --rule: #8a8a8a;
    --pattern-tone-a: #202023;
    --pattern-tone-b: #17171a;
  }
  * { box-sizing: border-box; margin: 0; padding: 0; }
  html, body {
    width: 1200px; height: 1108px; overflow: hidden;
    background: var(--page-bg);
    font-family: "Arimo", Arial, sans-serif;
  }
  .sheet {
    position: relative; width: 1200px; height: 1108px;
    display: flex; justify-content: center; align-items: center; gap: 80px;
  }
  .card {
    width: 430px; height: 700px; border-radius: 22px;
    position: relative; overflow: hidden;
  }
  .card--front {
    background: var(--card-bg); color: var(--ink);
    display: flex; flex-direction: column; align-items: center;
    padding-top: 44px; text-align: center;
  }
  .brand-mark {
    width: 200px; height: 200px; border-radius: 50%;
    border: 1.5px solid var(--ink-soft);
    display: flex; align-items: center; justify-content: center;
  }
  .brand-mark__name {
    font-size: 30px; font-weight: 400; line-height: 1.05; color: var(--ink);
  }
  .person-name {
    margin-top: 64px; font-size: 29px; font-weight: 700; letter-spacing: 0.5px;
  }
  .icon-rule {
    margin-top: 18px; width: 190px;
    display: flex; align-items: center; gap: 8px;
  }
  .icon-rule::before, .icon-rule::after {
    content: ""; flex: 1; height: 1px; background: var(--rule);
  }
  .contact-icon { width: 22px; height: 22px; display: block; }
  .contact-list { margin-top: 14px; font-size: 19px; line-height: 1.3; color: var(--ink); }
  .divider { width: 190px; height: 1px; background: var(--rule); margin: 16px 0 18px; }
  .company { font-size: 19px; font-weight: 700; }
  .address { font-size: 19px; line-height: 1.3; }

  .card--back { background: var(--card-back-bg); }
  .back-pattern {
    position: absolute; inset: 0;
    background: linear-gradient(160deg, var(--pattern-tone-a), var(--pattern-tone-b));
  }
  .back-mark {
    position: absolute; right: 78px; bottom: 150px;
    width: 92px; height: 92px; border-radius: 50%;
    border: 1px solid var(--ink-soft);
    display: flex; align-items: center; justify-content: center; text-align: center;
  }
  .back-mark__name { font-size: 14px; line-height: 1.05; color: var(--ink); }
</style>
</head>
<body>
<main class="sheet">
  <section class="card card--front">
    <div class="brand-mark">
      <span class="brand-mark__name">Heritage<br>Hollow</span>
    </div>
    <h1 class="person-name">MAYA TORVELL</h1>
    <div class="icon-rule">
      <svg class="contact-icon" viewBox="0 0 22 22" aria-label="Phone">
        <rect width="22" height="22" rx="3" fill="#f2f2f2"/>
        <path d="M6 5c1 0 2 2 2.4 3 .2.6-.8 1.2-.6 1.8.6 1.5 1.9 2.8 3.4 3.4.6.2 1.2-.8 1.8-.6 1 .4 3 1.4 3 2.4 0 1.2-1.4 2-2.6 2C8.6 17 5 13.4 5 8.6 5 7.4 4.8 5 6 5z" fill="#1f2022"/>
      </svg>
      <svg class="contact-icon" viewBox="0 0 22 22" aria-label="Email">
        <rect width="22" height="22" rx="3" fill="#f2f2f2"/>
        <rect x="4.5" y="6.5" width="13" height="9" fill="none" stroke="#1f2022" stroke-width="1.6"/>
        <path d="M4.5 6.5 11 12l6.5-5.5" fill="none" stroke="#1f2022" stroke-width="1.6"/>
      </svg>
      <svg class="contact-icon" viewBox="0 0 22 22" aria-label="Location">
        <rect width="22" height="22" rx="3" fill="#f2f2f2"/>
        <path d="M11 4a5 5 0 0 0-5 5c0 3.6 5 9 5 9s5-5.4 5-9a5 5 0 0 0-5-5z" fill="#1f2022"/>
        <circle cx="11" cy="9" r="1.8" fill="#f2f2f2"/>
      </svg>
    </div>
    <div class="contact-list">
      <p>02 6481 7395</p>
      <p>maya@kelvadtrading.com.au</p>
      <p>www.heritagehollow.com.au</p>
    </div>
    <div class="divider"></div>
    <p class="company">HERITAGE HOLLOW</p>
    <p class="address">PO Box Glenwarra NSW 2791</p>
  </section>

  <section class="card card--back">
    <div class="back-pattern" role="img" aria-label="Faint repeating brand pattern across the card back"></div>
    <div class="back-mark">
      <span class="back-mark__name">Heritage<br>Hollow</span>
    </div>
  </section>
</main>
</body>
</html>
```